Maple Bus Card

i own a building in the bronx ny - its called "Maple 7 on 2 HDFC"i want a classy logo / business card - nothing too religuous but it is like a family there - its a large apartment building - colors i like dark red, black, medium shade of gray also reg business card stuff tel # 914-555-0173 address 4738 Larkwell Ave Dunmore NY 10599 Email fijosh@aol.comslogan - " Under one roof we stand "i can send u a picture of the building for the backside

```html
<!DOCTYPE html>
<html lang="en">
<head>
<meta charset="UTF-8">
<title>Maple 7 on 2 HDFC — Business Card</title>
<link rel="stylesheet" href="https://fonts.googleapis.com/css2?family=Open+Sans:wght@400;600;700&display=swap">
<style>
  :root {
    --brand-red: #d40c0f;
    --ink: #2b2b2b;
    --ink-soft: #3c3c3c;
    --paper: #ffffff;
    --backdrop: #d9d9d9;
    --faint-gray: #ececec;
  }
  * { margin: 0; padding: 0; box-sizing: border-box; }
  html, body { width: 1200px; height: 900px; overflow: hidden; }
  body {
    background: var(--backdrop);
    font-family: "Open Sans", Arial, sans-serif;
    position: relative;
  }
  .card {
    position: absolute;
    width: 560px;
    height: 320px;
    border-radius: 26px;
    overflow: hidden;
  }
  /* Front */
  .card--front {
    left: 70px; top: 110px;
    background: var(--brand-red);
    color: var(--paper);
  }
  .front-mark {
    position: absolute;
    left: 0; right: 0; top: 104px;
    display: flex; align-items: center; justify-content: center; gap: 18px;
  }
  .mark-dot {
    width: 54px; height: 54px; border-radius: 50%;
    background: var(--paper);
    flex: none;
  }
  .front-mark .brand-name {
    font-weight: 700; font-size: 38px; line-height: 1; letter-spacing: -0.5px;
  }
  .slogan {
    position: absolute; left: 0; right: 0; top: 238px;
    text-align: center;
    font-size: 15px; font-weight: 600; letter-spacing: 2.6px;
  }
  /* Back */
  .card--back {
    left: 570px; top: 470px;
    background: var(--paper);
    color: var(--ink);
  }
  .back-decor {
    position: absolute; right: -70px; top: -60px;
    width: 250px; height: 250px; border-radius: 50%;
    background: var(--faint-gray);
  }
  .back-mark {
    position: absolute; left: 34px; top: 48px;
    display: flex; align-items: center; gap: 14px;
  }
  .back-mark .mark-dot { background: var(--brand-red); width: 46px; height: 46px; }
  .back-mark .brand-name {
    color: var(--brand-red);
    font-weight: 700; font-size: 36px; line-height: 1; letter-spacing: -0.5px;
  }
  .address {
    position: absolute; right: 30px; top: 128px;
    text-align: right;
    font-size: 17px; line-height: 1.3; color: var(--ink-soft);
  }
  .contact {
    position: absolute; left: 38px; top: 184px;
    font-size: 17px; line-height: 1.35; color: var(--ink-soft);
  }
  .contact .person {
    color: var(--brand-red); font-weight: 600; font-size: 18px; letter-spacing: 0.4px;
  }
  .contact-line { display: flex; align-items: center; gap: 8px; }
  .contact-line svg { width: 14px; height: 14px; fill: var(--brand-red); flex: none; }
</style>
</head>
<body>

  <section class="card card--front" aria-label="Business card front">
    <div class="front-mark">
      <span class="mark-dot"></span>
      <span class="brand-name">Maple 7 on 2 HDFC</span>
    </div>
    <p class="slogan">UNDER ONE ROOF WE STAND</p>
  </section>

  <section class="card card--back" aria-label="Business card back">
    <div class="back-decor"></div>
    <div class="back-mark">
      <span class="mark-dot"></span>
      <span class="brand-name">Maple 7 on 2 HDFC</span>
    </div>
    <p class="address">4738 Larkwell Ave<br>Dunmore NY 10599</p>
    <div class="contact">
      <p class="person">DORIAN KELLER</p>
      <p class="role">Managing Director</p>
      <p class="contact-line">
        <svg viewBox="0 0 24 24" aria-hidden="true"><path d="M6.6 10.8a15.1 15.1 0 0 0 6.6 6.6l2.2-2.2c.3-.3.7-.4 1-.2 1.1.4 2.3.6 3.6.6.6 0 1 .4 1 1V20c0 .6-.4 1-1 1A17 17 0 0 1 3 4c0-.6.4-1 1-1h3.5c.6 0 1 .4 1 1 0 1.3.2 2.5.6 3.6.1.3 0 .7-.2 1z"/></svg>
        914-555-0173
      </p>
      <p class="contact-line">
        <svg viewBox="0 0 24 24" aria-hidden="true"><path d="M2 5h20v14H2z M2 5l10 8 10-8" stroke="#fff" stroke-width="1.6"/></svg>
        mavreld@quintmail.com
      </p>
    </div>
  </section>

</body>
</html>
```